20 year old business card needs re-design

We need to redesign our corporate business card look. We need something that appears more modern, eye catchy but professional.

Target Market(s)

manufacturing industry

Industry/Entity Type

Manufacturer

Contact Information for Business Card

One side can have the logo. Other side can have contact information.

Font styles to use
Serif

Colors
3277b5
33b8a4
ffffff

Requirements
Must have
• Eye catchy - need to standout from the crowd. company logo cannot change. Full name, job title, phone number and email address.
Should not have
• Fax, business address is not necessary.

```html
<!DOCTYPE html>
<html lang="en">
<head>
<meta charset="utf-8">
<title>Norvale Industrial — Business Card</title>
<link href="https://fonts.googleapis.com/css2?family=Mulish:wght@400;600;700;800&display=swap" rel="stylesheet">
<style>
  :root {
    --brand-blue: #3277b5;
    --brand-teal: #33b8a4;
    --paper: #ffffff;
    --ink: #1f1f1f;
    --muted: #5e6266;
    --backdrop: #2a2a2a;
  }
  * { box-sizing: border-box; margin: 0; padding: 0; }
  html, body {
    width: 1200px; height: 897px; overflow: hidden;
    background: var(--backdrop);
    font-family: "Mulish", sans-serif;
  }
  .stage { position: relative; width: 1200px; height: 897px; }

  .card { position: absolute; overflow: hidden; }

  /* Front side */
  .card-front {
    left: 354px; top: 162px; width: 486px; height: 278px;
    background: linear-gradient(160deg, #3a80bd 0%, var(--brand-blue) 55%, #2e6fab 100%);
    color: var(--paper);
  }
  .front-wordmark {
    position: absolute; left: 0; right: 0; top: 118px;
    text-align: center;
    font-size: 34px; font-weight: 800; letter-spacing: -0.5px;
    color: var(--paper);
  }
  .front-url {
    position: absolute; left: 0; right: 0; top: 242px;
    text-align: center; font-size: 11px; letter-spacing: 1.2px;
  }

  /* Back side */
  .card-back {
    left: 348px; top: 468px; width: 492px; height: 278px;
    background: var(--paper);
  }
  .back-wordmark {
    position: absolute; left: 24px; top: 22px;
    font-size: 26px; font-weight: 800; letter-spacing: -0.4px;
    color: var(--ink);
  }
  .holder {
    position: absolute; right: 22px; top: 148px; text-align: right;
  }
  .holder-name {
    font-size: 17px; font-weight: 700; letter-spacing: 0.6px;
    color: var(--brand-blue);
  }
  .holder-title { font-size: 10.5px; color: var(--muted); margin-top: 1px; }
  .edge-tab {
    position: absolute; right: 0; top: 152px; width: 6px; height: 28px;
    background: var(--brand-teal);
  }
  .divider {
    position: absolute; left: 26px; width: 444px; top: 192px; height: 1.5px;
    background: var(--brand-teal);
  }
  .contact-list {
    position: absolute; left: 26px; top: 210px; list-style: none;
  }
  .contact-list li {
    display: flex; align-items: center; gap: 8px;
    font-size: 11px; color: var(--muted); height: 16px;
  }
  .contact-list svg { width: 9px; height: 9px; fill: none; stroke: var(--brand-blue); stroke-width: 1.6; }
  .locations {
    position: absolute; right: 22px; top: 210px; text-align: right;
    font-size: 11px; color: var(--muted); line-height: 15px;
  }
  .base-band { position: absolute; left: 0; bottom: 0; width: 100%; height: 6px; display: flex; }
  .base-band .teal { width: 244px; background: var(--brand-teal); }
  .base-band .blue { flex: 1; background: var(--brand-blue); }
</style>
</head>
<body>
<main class="stage">
  <section class="card card-front" aria-label="Card front">
    <div class="front-wordmark">Norvale Industrial</div>
    <div class="front-url">norvaleindustrial.com</div>
  </section>

  <section class="card card-back" aria-label="Card back">
    <div class="back-wordmark">Norvale Industrial</div>

    <div class="holder">
      <div class="holder-name">Dan Merrick</div>
      <div class="holder-title">Sr. Project Manager</div>
    </div>
    <div class="edge-tab"></div>
    <div class="divider"></div>

    <ul class="contact-list">
      <li>
        <svg viewBox="0 0 10 10"><rect x="2.5" y="0.8" width="5" height="8.4" rx="0.8"/></svg>
        555-014-2280 xt 104
      </li>
      <li>
        <svg viewBox="0 0 10 10"><rect x="0.8" y="2" width="8.4" height="6"/><path d="M0.8 2 L5 5.5 L9.2 2"/></svg>
        dan@norvaleindustrial.com
      </li>
      <li>
        <svg viewBox="0 0 10 10"><circle cx="4.2" cy="4.2" r="3"/><path d="M6.4 6.4 L9.2 9.2"/></svg>
        NorvaleIndustrial.com
      </li>
    </ul>

    <div class="locations">
      Offices &amp; Warehousing:<br>
      USA - Taiwan - Mexico
    </div>

    <div class="base-band"><span class="teal"></span><span class="blue"></span></div>
  </section>
</main>
</body>
</html>
```